SavannaPlate Web Page Templates

I need two templates designed for a wholesale food/catering business, one template for the home page and the other for detail pages. The overall template should be a simple, clean and clear design. I have provided the existing logo to which the templates should directly relate.
SavannaPlate supplies food based upon traditional Ghanian recipes to a number of stores across Canberra. In addition, SavannaPlate offers catering for public and private functions across the Canberra region.
The colours in the logo represent the national colours of Ghana (yellow, green, red and black) and the website content will also include traditional Ghanian Kente patterns which will add further colour elements to the site. On this basis, the template design needs to be fairly sparse so as not to compete with the colourful content of the website detail pages.
There is no requirement for specific pages to be designed, as these will be handled in the CMS implementation.
The information provided in the Word document is only designed to provide a sense of the intended content of the website, not as a requirement for specific pages to be produced.

Target Market(s)

Retail/Wholesale food

Number of Pages Required

2 page

Font styles to use
Serif

Colors

Designer to choose colors to be used in the design.

Requirements
Must have
• Template must accommodate a responsive design
• The logo provided will form the cornerstone of the design
Nice to have
• There
Should not have
• Please do not solicit for extra work or for alternative logo design.

```html
<!DOCTYPE html>
<html lang="en">
<head>
<meta charset="utf-8">
<title>SavannaPlate – Home</title>
<link href="https://fonts.googleapis.com/css2?family=Exo+2:wght@500;600;700;800&family=Noto+Serif:ital,wght@0,400;0,700;1,400&display=swap" rel="stylesheet">
<style>
:root{
  --orange:#f4592b;
  --orange-soft:#f57a3a;
  --ink:#222222;
  --text:#666666;
  --white:#ffffff;
  --night:#151b24;
  --line:#e9e9e9;
}
*{box-sizing:border-box;margin:0;padding:0}
html,body{width:1200px;height:3460px;overflow:hidden}
body{position:relative;background:var(--white);font-family:"Noto Serif",serif;color:var(--text)}
.abs{position:absolute}
.btn{position:absolute;z-index:2;background:var(--orange);color:var(--white);font-family:"Noto Serif",serif;font-weight:700;font-size:13px;border-radius:20px;height:36px;line-height:36px;text-align:center;text-transform:uppercase}
.heading{font-family:"Exo 2",sans-serif;font-weight:700;color:var(--ink)}
.rule{position:absolute;height:2px;width:24px;background:var(--orange)}

/* top bar */
.topbar{left:0;top:0;width:1200px;height:38px;background:var(--orange);color:var(--white);font-size:12px}
.topbar span{position:absolute;top:11px}
.social{position:absolute;top:11px;width:15px;height:15px;border-radius:50%;border:1.5px solid var(--white)}

/* nav */
.nav{left:0;top:38px;width:1200px;height:76px;background:var(--white)}
.brand{position:absolute;left:161px;top:22px;font-family:"Noto Serif",serif;font-weight:700;font-size:24px;color:var(--orange)}
.menu a{position:absolute;top:26px;font-size:13px;color:#333;text-decoration:none;height:26px;line-height:26px}
.menu a.active{background:var(--orange);color:var(--white);border-radius:14px;padding:0 18px}
.search{position:absolute;left:1026px;top:31px}

/* hero */
.hero{left:0;top:114px;width:1200px;height:486px;background:radial-gradient(ellipse at 62% 45%,#7a3c18 0%,#4a2614 35%,#2e2320 65%,#1f1b19 100%)}
.hero h1{position:absolute;left:158px;top:155px;font-family:"Exo 2",sans-serif;font-weight:800;font-size:46px;line-height:58px;color:var(--white)}
.dots3{position:absolute;top:454px;left:544px}
.dots3 i{display:inline-block;width:30px;height:3px;background:rgba(255,255,255,.5);margin-right:8px}
.dots3 i.on{background:var(--orange)}

/* about */
.spice-left{left:0;top:640px;width:140px;height:280px;background:radial-gradient(circle at 20% 50%,#c66a25 0%,#e8d3c0 40%,#fff 70%)}
.about-title{left:161px;top:688px;font-size:26px}
.about-text{left:161px;top:752px;width:338px;font-size:12.5px;line-height:19.5px}
.about-text p{margin-bottom:19px}
.about-frame{left:587px;top:680px;width:428px;height:355px;border:6px solid var(--orange);border-radius:10px}
.about-photo{left:610px;top:656px;width:428px;height:358px;border-radius:10px;background:radial-gradient(ellipse at 55% 50%,#8d3a1e 0%,#c07850 30%,#e9e7e4 55%,#cfcac4 100%)}
.chef{left:145px;top:1060px;width:890px;height:290px;background:radial-gradient(ellipse at 50% 60%,#c9a68a 0%,#e8d6c4 35%,#fff 70%)}

/* band */
.band{left:0;top:1350px;width:1200px;height:384px;background:linear-gradient(90deg,#131a25 0%,#1c2430 55%,#2a2620 100%)}
.band h2{position:absolute;left:0;width:760px;top:66px;text-align:center;font-family:"Exo 2",sans-serif;font-weight:700;font-size:25px;color:var(--white)}
.band .rule{left:367px;top:115px;background:#cfcfcf}
.stat{position:absolute;top:140px;width:180px;text-align:center;color:var(--white)}
.stat svg{display:block;margin:0 auto 16px}
.stat b{display:block;font-family:"Exo 2",sans-serif;font-weight:700;font-size:15px;letter-spacing:.2px}
.stat em{display:block;font-style:normal;font-size:27px;color:var(--orange-soft);margin-top:14px}
.video{left:658px;top:1395px;width:427px;height:296px;border:3px solid var(--white);border-radius:8px;background:radial-gradient(ellipse at 50% 55%,#6b6a66 0%,#3d3c3a 45%,#242321 100%)}
.play{position:absolute;left:179px;top:112px}

/* menu */
.menu-title{left:0;width:1200px;top:1770px;text-align:center;font-size:25px}
.item{position:absolute;z-index:1;width:410px;height:97px}
.item .pic{position:absolute;left:0;top:0;width:150px;height:97px}
.item h3{position:absolute;left:167px;top:14px;font-family:"Exo 2",sans-serif;font-weight:500;font-size:14px;color:#333}
.item .price{position:absolute;right:0;top:12px;font-size:16px;color:var(--orange)}
.item p{position:absolute;left:167px;top:40px;width:245px;font-size:11px;line-height:20px;color:#888}
.spice-menu-left{left:0;top:1740px;width:120px;height:300px;background:radial-gradient(circle at 20% 45%,#c9561f 0%,#ecd6c2 38%,#fff 68%)}
.spice-right{left:1050px;top:2075px;width:150px;height:210px;background:radial-gradient(circle at 75% 40%,#e49a3a 0%,#f1dcc3 35%,#fff 70%)}

/* testimonial */
.quote{left:0;top:2285px;width:1200px;height:364px;background:radial-gradient(ellipse at 30% 55%,#4f6b2c 0%,#3a3424 35%,#2b2925 70%,#20201f 100%)}
.quote h2{position:absolute;left:0;width:1200px;top:52px;text-align:center;font-family:"Exo 2",sans-serif;font-weight:700;font-size:26px;color:var(--white)}
.avatar{position:absolute;left:554px;top:92px;width:88px;height:88px;border-radius:50%;border:3px solid var(--white);background:radial-gradient(circle,#d8b59a,#8e6e58)}
.quote p{position:absolute;left:370px;width:460px;top:196px;text-align:center;font-style:italic;font-size:13px;line-height:20px;color:var(--white)}
.quote .who{position:absolute;left:0;width:1200px;top:258px;text-align:center;color:var(--white);font-size:13px}
.quote .role{position:absolute;left:0;width:1200px;top:282px;text-align:center;color:var(--white);font-size:10px}
.qdots{position:absolute;left:579px;top:310px}
.qdots i{display:inline-block;width:9px;height:9px;border:1.5px solid var(--orange);border-radius:50%;margin-right:5px}

/* features */
.feat-title{left:0;width:1200px;top:2688px;text-align:center;font-size:25px}
.feat-frame{left:156px;top:2812px;width:420px;height:308px;border:2px solid var(--orange);transform:rotate(-3deg)}
.feat-photo{left:192px;top:2826px;width:375px;height:301px;background:radial-gradient(ellipse at 45% 70%,#7a5436 0%,#bdb7b0 30%,#3d3a38 75%)}
.fdots{position:absolute;left:355px;top:3149px}
.fdots i{display:inline-block;width:11px;height:11px;border-radius:50%;background:var(--orange);margin-right:8px}
.fdots i.off{background:none;border:1.5px solid var(--orange)}
.card{position:absolute;width:203px;height:153px;background:var(--white);box-shadow:0 2px 10px rgba(0,0,0,.12);text-align:center}
.card .ico{position:absolute;left:76px;top:-24px;width:50px;height:50px;border-radius:50%;background:var(--white);box-shadow:0 2px 8px rgba(0,0,0,.12)}
.card .ico svg{margin-top:14px}
.card h4{margin-top:55px;font-family:"Exo 2",sans-serif;font-weight:600;font-size:14px;color:#333}
.card p{margin:12px 14px 0;font-size:11px;line-height:20px;color:#888}

/* footer */
.footer{left:0;top:3208px;width:1200px;height:212px;background:radial-gradient(ellipse at 60% 50%,#5a2f1c 0%,#3a2a24 45%,#2a2624 100%)}
.footer .brand{left:0;width:1200px;text-align:center;top:34px;font-size:26px}
.fnav{position:absolute;top:103px;left:0;width:1200px;text-align:center}
.fnav a{color:var(--white);text-decoration:none;font-size:13px;margin:0 15px}
.fcontact{position:absolute;top:138px;left:0;width:1200px;text-align:center;color:var(--white);font-size:13px}
.fcontact span{display:inline-flex;align-items:center;margin:0 10px}
.fcontact svg{margin-right:8px}
.bottom{left:0;top:3420px;width:1200px;height:40px;background:var(--orange);color:var(--white);font-size:11px}
.bottom span{position:absolute;top:13px}
</style>
</head>
<body>

<header class="abs topbar">
  <span style="left:161px">&#9742; 555-014-2468</span>
  <span style="left:828px">&#9993; hello@savannaplate.com</span>
  <i class="social" style="left:1003px"></i>
  <i class="social" style="left:1024px"></i>
</header>

<nav class="abs nav">
  <div class="brand">SavannaPlate</div>
  <div class="menu">
    <a class="active" style="left:599px">Home</a>
    <a style="left:690px">About Us</a>
    <a style="left:776px">Catering</a>
    <a style="left:863px">Menu</a>
    <a style="left:930px">Contact Us</a>
  </div>
  <svg class="search" width="12" height="12" viewBox="0 0 12 12"><circle cx="5" cy="5" r="3.8" fill="none" stroke="#333" stroke-width="1.6"/><line x1="8" y1="8" x2="11" y2="11" stroke="#333" stroke-width="1.8"/></svg>
</nav>

<section class="abs hero" role="img" aria-label="Pot of spiced stew with pomegranate seeds on a dark wooden table">
  <h1>HAVE A TASTE!<br>ENJOY!!</h1>
  <div class="btn" style="left:161px;top:282px;width:128px">Contact Us</div>
  <div class="dots3"><i></i><i class="on"></i><i></i></div>
</section>

<div class="abs spice-left" role="img" aria-label="Bowls of spices and chillies"></div>
<h2 class="abs heading about-title">About Us</h2>
<div class="rule" style="left:161px;top:733px"></div>
<div class="abs about-text">
  <p>Lorem Ipsum is simply dummy text of the printing and typesetting industry. Lorem Ipsum has been the industry's standard dummy text ever since the 1500s, when an unknown printer took a galley of type and scrambled it to make a type specimen book. It has survived not only five centuries, but also the leap into electronic typesetting.</p>
  <p>remaining essentially unchanged. It was popularised in the 1960s with the release ohing software like Aldus.</p>
</div>
<div class="btn" style="left:161px;top:963px;width:128px">Contact Us</div>
<div class="abs about-frame"></div>
<div class="abs about-photo" role="img" aria-label="Bowl of beef and bean stew"></div>
<div class="abs chef" role="img" aria-label="Chef with knife behind fruit, vegetables and a glass of wine"></div>

<section class="abs band">
  <h2>We Are Born To Serve You</h2>
  <div class="rule"></div>
  <div class="stat" style="left:87px">
    <svg width="42" height="42" viewBox="0 0 42 42" fill="none" stroke="#f4592b" stroke-width="2"><path d="M6 28h30M9 28a12 12 0 0 1 24 0M21 13v3M17 32h8"/><circle cx="21" cy="11" r="2"/></svg>
    <b>AMAZING DISHES</b><em>20+</em>
  </div>
  <div class="stat" style="left:287px">
    <svg width="42" height="42" viewBox="0 0 42 42" fill="none" stroke="#f4592b" stroke-width="2"><path d="M13 24a7 7 0 1 1 5-12 7 7 0 0 1 12 2 6 6 0 1 1 0 10v10H13z"/><path d="M13 30h17"/></svg>
    <b>SATISFIED STAFF</b><em>15+</em>
  </div>
  <div class="stat" style="left:490px">
    <svg width="42" height="42" viewBox="0 0 42 42" fill="none" stroke="#f4592b" stroke-width="2"><circle cx="21" cy="23" r="14"/><path d="M21 23l5-5M17 6h8"/></svg>
    <b>WORK HOURS</b><em>24</em>
  </div>
  <div class="btn" style="left:315px;top:290px;width:128px">Served Now</div>
  <div class="abs video" role="img" aria-label="Chef tossing food in a pan in a kitchen" style="top:45px">
    <svg class="play" width="66" height="66" viewBox="0 0 66 66"><circle cx="33" cy="33" r="30" fill="none" stroke="#fff" stroke-width="3"/><path d="M26 20l20 13-20 13z" fill="#fff"/></svg>
  </div>
</section>

<div class="abs spice-menu-left" role="img" aria-label="Bowls of ground spices"></div>
<div class="abs spice-right" role="img" aria-label="Scattered spices and herbs"></div>

<h2 class="abs heading menu-title">Our Special Menu</h2>
<div class="rule" style="left:588px;top:1817px"></div>

<div class="item" style="left:161px;top:1841px"><div class="pic" role="img" aria-label="Coconut sweet" style="background:linear-gradient(135deg,#c48a5c,#efe4d4)"></div><h3>Coconut Sweet</h3><span class="price">$15.00</span><p>Lorem ipsum dolor sit amet, consectetur Dolor adipiscing elit, sed do eiusmod tempor..</p></div>
<div class="item" style="left:611px;top:1841px"><div class="pic" role="img" aria-label="Spinach casserole" style="background:linear-gradient(135deg,#7a3a22,#d4c6b8)"></div><h3>Spinach Casserole</h3><span class="price">$15.00</span><p>Lorem ipsum dolor sit amet, consectetur Dolor adipiscing elit, sed do eiusmod tempor..</p></div>
<div class="item" style="left:161px;top:1962px"><div class="pic" role="img" aria-label="Black-eyed beans snacks" style="background:linear-gradient(135deg,#d19a2a,#2a5c8a)"></div><h3>Black-eyed Beans Snacks</h3><span class="price">$15.00</span><p>Lorem ipsum dolor sit amet, consectetur Dolor adipiscing elit, sed do eiusmod tempor..</p></div>
<div class="item" style="left:611px;top:1962px"><div class="pic" role="img" aria-label="Chicken casserole" style="background:linear-gradient(135deg,#c0622a,#e2c7a0)"></div><h3>Chicken Casserole</h3><span class="price">$15.00</span><p>Lorem ipsum dolor sit amet, consectetur Dolor adipiscing elit, sed do eiusmod tempor..</p></div>
<div class="item" style="left:161px;top:2083px"><div class="pic" role="img" aria-label="Spicy beef casserole" style="background:linear-gradient(135deg,#6e2c1a,#c9b6a4)"></div><h3>Spicy Beef Casserole</h3><span class="price">$15.00</span><p>Lorem ipsum dolor sit amet, consectetur Dolor adipiscing elit, sed do eiusmod tempor..</p></div>
<div class="item" style="left:611px;top:2083px"><div class="pic" role="img" aria-label="Ghanaian chilli sauce" style="background:linear-gradient(135deg,#3a2620,#8a2a14)"></div><h3>Ghanaian Chilli Sauce</h3><span class="price">$15.00</span><p>Lorem ipsum dolor sit amet, consectetur Dolor adipiscing elit, sed do eiusmod tempor..</p></div>

<div class="btn" style="left:537px;top:2203px;width:126px">View All</div>

<section class="abs quote" role="img" aria-label="Table with fresh lettuce, tomatoes and grilled chicken">
  <h2>They Said</h2>
  <div class="avatar" role="img" aria-label="Customer portrait"></div>
  <p>There are many variations of passages of Lorem Ipsum available, but the majority have suffered alteration Lorem Ipsum is simply dummy text.</p>
  <div class="who">MARA ELLISON</div>
  <div class="role">CUSTOMER</div>
  <div class="qdots"><i></i><i></i><i></i></div>
</section>

<h2 class="abs heading feat-title">Our Some Features</h2>
<div class="rule" style="left:588px;top:2735px"></div>
<div class="abs feat-frame"></div>
<div class="abs feat-photo" role="img" aria-label="Waiter presenting a plated dish"></div>
<div class="fdots"><i></i><i></i><i class="off"></i></div>

<div class="card" style="left:618px;top:2793px"><div class="ico"><svg width="22" height="22" viewBox="0 0 22 22"><rect x="4" y="1" width="14" height="20" rx="2" fill="#f4592b"/><path d="M7 7h8M7 11h8M7 15h5" stroke="#fff" stroke-width="1.5"/></svg></div><h4>VARIOUS MENU</h4><p>Lorem ipsum dolor sit amet, consectetur Dolor adipiscing elit, sed do eiusmod tempor..</p></div>
<div class="card" style="left:843px;top:2793px"><div class="ico"><svg width="22" height="22" viewBox="0 0 22 22"><path d="M2 2h18l-9 10z" fill="#f4592b"/><path d="M11 11v8M6 20h10" stroke="#f4592b" stroke-width="2"/></svg></div><h4>FRESH DISHES</h4><p>Lorem ipsum dolor sit amet, consectetur Dolor adipiscing elit, sed do eiusmod tempor..</p></div>
<div class="card" style="left:618px;top:2994px"><div class="ico"><svg width="22" height="22" viewBox="0 0 22 22"><rect x="2" y="8" width="18" height="4" fill="#f4592b"/><rect x="4" y="12" width="14" height="9" fill="#f4592b"/><path d="M11 8v13" stroke="#fff" stroke-width="2"/><path d="M11 8c-2-5-7-5-6-1M11 8c2-5 7-5 6-1" stroke="#f4592b" stroke-width="1.6" fill="none"/></svg></div><h4>WELL SERVICES</h4><p>Lorem ipsum dolor sit amet, consectetur Dolor adipiscing elit, sed do eiusmod tempor..</p></div>
<div class="card" style="left:843px;top:2994px"><div class="ico"><svg width="24" height="22" viewBox="0 0 24 22"><rect x="1" y="5" width="14" height="10" fill="#f4592b"/><path d="M15 8h5l3 4v3h-8z" fill="#f4592b"/><circle cx="6" cy="17" r="2.5" fill="#f4592b"/><circle cx="18" cy="17" r="2.5" fill="#f4592b"/></svg></div><h4>FAST DELIVERY</h4><p>Lorem ipsum dolor sit amet, consectetur Dolor adipiscing elit, sed do eiusmod tempor..</p></div>

<footer class="abs footer" role="img" aria-label="Plated food in soft focus">
  <div class="brand">SavannaPlate</div>
  <div class="fnav"><a>Home</a><a>About Us</a><a>Catering</a><a>Menu</a><a>Contact Us</a></div>
  <div class="fcontact">
    <span><svg width="22" height="22" viewBox="0 0 22 22"><circle cx="11" cy="11" r="10" fill="none" stroke="#f4592b" stroke-width="1.5"/><path d="M7.5 6.5l2 2-1 1.5c.8 1.6 2 2.8 3.5 3.5l1.5-1 2 2-1.5 1.5c-3.5-.5-7.5-4.5-8-8z" fill="#fff"/></svg>555-014-2468</span>
    <span><svg width="22" height="22" viewBox="0 0 22 22"><circle cx="11" cy="11" r="10" fill="#f4592b"/><rect x="6" y="7.5" width="10" height="7" fill="#fff"/><path d="M6 7.5l5 4 5-4" stroke="#f4592b" fill="none"/></svg>hello@savannaplate.com</span>
  </div>
</footer>

<div class="abs bottom">
  <span style="left:161px">Copyright SavannaPlate 2019 | All Rights Reserved.</span>
  <span style="left:834px">Privacy Policy &nbsp;&nbsp;| &nbsp;&nbsp;Terms &amp; Conditions</span>
</div>

</body>
</html>
```